Local Roofing Company Billboard Design

We need a billboard design for an 8' x 32' billboard. This billboard would need to be easily readable and stand out well.
I have uploaded a design that we like - simple, readable, and gets the point across. We do NOT want the $1000 off offer included.
We are looking for a black background with white copy so it will stand out. We want the following on the billboard:
Brindlewick Roofing logo
brindlewick-roofing.example (optional)
555.214.7730 (mandatory)
Photo is optional, depends on how it all lays out
Production file must comply with layout requirements (uploaded).
Target Market(s)
Homeowners
Font styles to use
Other font styles liked:
- match font from logo
Colors
Designer to choose colors to be used in the design.
Requirements
Must have
- Black background, white copy, logo must be large and legible. Colors used must match our logo colors.

```html
<!DOCTYPE html>
<html lang="en">
<head>
<meta charset="utf-8">
<title>Brindlewick Roofing Billboard</title>
<link rel="stylesheet" href="https://fonts.googleapis.com/css2?family=Montserrat:wght@500;700&family=Oswald:wght@600&display=swap">
<style>
  :root {
    --ink: #000000;
    --paper: #ffffff;
    --brand-orange: #e8581c;
    --sky-light: #dbe9f5;
    --sky-mid: #a9c6e2;
    --roof-slate: #4a5363;
    --roof-dark: #343b48;
    --canvas-bg: #ffffff;
  }
  html, body {
    margin: 0;
    padding: 0;
    width: 1200px;
    height: 1051px;
    overflow: hidden;
    background: var(--canvas-bg);
  }
  .canvas {
    position: relative;
    width: 1200px;
    height: 1051px;
  }
  .billboard {
    position: absolute;
    left: 50px;
    top: 388px;
    width: 1100px;
    height: 275px;
    box-shadow: 0 24px 48px rgba(0, 0, 0, 0.22);
  }
  .billboard svg {
    display: block;
    width: 100%;
    height: 100%;
  }
  .brand-name {
    font-family: "Montserrat", sans-serif;
    font-weight: 700;
    fill: var(--paper);
  }
  .website {
    font-family: "Montserrat", sans-serif;
    font-weight: 500;
    fill: var(--paper);
  }
  .phone-number {
    font-family: "Oswald", sans-serif;
    font-weight: 600;
    fill: var(--paper);
  }
  .panel-black { fill: var(--ink); }
  .band-orange { fill: var(--brand-orange); }
  .stripe-white { fill: var(--paper); }
  .icon-fill { fill: var(--paper); }
  .icon-stroke { fill: none; stroke: var(--paper); }
</style>
</head>
<body>
<main class="canvas">
  <section class="billboard">
    <svg viewBox="0 0 1764 441" preserveAspectRatio="none">
      <defs>
        <linearGradient id="house-photo-tone" x1="0" y1="0" x2="0" y2="1">
          <stop offset="0" stop-color="var(--sky-light)"/>
          <stop offset="0.35" stop-color="var(--sky-mid)"/>
          <stop offset="0.55" stop-color="var(--roof-slate)"/>
          <stop offset="1" stop-color="var(--roof-dark)"/>
        </linearGradient>
      </defs>

      <rect class="house-photo" x="0" y="0" width="1000" height="321" fill="url(#house-photo-tone)" role="img" aria-label="Photo of a white house with a dark slate tile roof and brick chimney under a blue sky"/>

      <polygon class="band-orange accent-stripe" points="970,0 993,0 798,253 775,253"/>
      <polygon class="panel-black brand-panel" points="993,0 1764,0 1764,253 798,253"/>
      <polygon class="stripe-white divider-stripe" points="783,253 806,253 661,441 638,441"/>
      <polygon class="band-orange phone-band" points="806,253 1764,253 1764,441 661,441"/>
      <polygon class="panel-black website-band" points="0,321 731,321 638,441 0,441"/>

      <text class="brand-name" x="1360" y="150" font-size="64" text-anchor="middle">Brindlewick Roofing</text>

      <g class="website-icon" transform="translate(55,357)">
        <rect class="icon-stroke" x="5" y="3" width="44" height="30" rx="2" stroke-width="6"/>
        <rect class="icon-fill" x="0" y="38" width="56" height="7" rx="2"/>
      </g>
      <text class="website" x="135" y="393" font-size="36" textLength="500" lengthAdjust="spacingAndGlyphs">Brindlewick-Roofing.example</text>

      <g class="phone-icon" transform="translate(805,302)">
        <path class="icon-fill" transform="scale(3.6)" d="M6.62 10.79c1.44 2.83 3.76 5.14 6.59 6.59l2.2-2.2c.27-.27.67-.36 1.02-.24 1.12.37 2.33.57 3.57.57.55 0 1 .45 1 1V20c0 .55-.45 1-1 1-9.39 0-17-7.610-17-17 0-.55.45-1 1-1h3.5c.55 0 1 .45 1 1 0 1.25.2 2.45.57 3.57.11.35.03.74-.25 1.02l-2.2 2.2z"/>
        <path class="icon-stroke" d="M48 22 A18 18 0 0 1 62 38" stroke-width="6" stroke-linecap="round"/>
        <path class="icon-stroke" d="M50 6 A34 34 0 0 1 78 36" stroke-width="6" stroke-linecap="round"/>
      </g>
      <text class="phone-number" x="918" y="400" font-size="150" textLength="780" lengthAdjust="spacingAndGlyphs">555-214-7730</text>
    </svg>
  </section>
</main>
</body>
</html>
```